Vellisant - Quality health delivered at your door

Vellisant offers home and Community Based Services for adults who wish to continue live independently in their communities. We increase accessibility to health care, reduce health care delivery gap, reduce mortality and morbidity, reduce health while promoting healthy living in the comfort of our patients communities or homes.

We provide on site services and deliver high quality healthcare at your door. Our experienced physicians coordinate care with our certified nurse practitioners and provide chronic care management, physical therapy, rehabilitation and medications management.

Target Market(s)

Older population living in independent living facilities

Industry/Entity Type

Health Care

Contact Information for Business Card

Vellisant

Number of Pages Required

4 page

Font styles to use
Sans Serif

Colors

Designer to choose colors to be used in the design.

```html
<!DOCTYPE html>
<html lang="en">
<head>
<meta charset="utf-8">
<title>Vellisant - Quality health delivered at your door</title>
<link rel="stylesheet" href="https://fonts.googleapis.com/css2?family=Roboto:ital,wght@0,300;0,400;0,500;0,700;1,400&family=Roboto+Condensed:wght@400;700&display=swap">
<style>
:root{
  --green:#4e7f12;
  --green-light:#6c9f1f;
  --green-dark:#1f3b0c;
  --orange:#f39c12;
  --ink:#333;
  --muted:#777;
  --grey-band:#eeeeee;
  --footer:#1b1b1b;
  --white:#fff;
}
*{margin:0;padding:0;box-sizing:border-box}
html,body{width:1200px;height:2961px;overflow:hidden;background:var(--white)}
body{font-family:"Roboto",sans-serif;color:var(--ink);position:relative}
.abs{position:absolute}
/* header */
.header{top:0;left:0;width:1200px;height:158px}
.contact-top{left:98px;top:64px;display:flex;gap:14px;align-items:center;font-size:14px;color:#444;line-height:20px}
.contact-top .ring{width:34px;height:34px;border:1px solid #ccc;border-radius:50%;display:flex;align-items:center;justify-content:center}
.contact-top small{font-size:13px;color:#555}
.brand{left:450px;width:300px;top:58px;text-align:center}
.brand .name{font-size:32px;font-weight:500;color:var(--green-dark);letter-spacing:1px;line-height:40px}
.search{left:868px;top:62px;width:232px;height:36px;border:1px solid #ccc;border-radius:3px;display:flex;align-items:center;justify-content:space-between;padding:0 12px;font-size:12px;color:#666}
/* nav */
.nav{top:158px;left:0;width:1200px;height:52px;background:linear-gradient(#6e9f25,#3f6e0e);display:flex;padding-left:100px}
.nav a{font-family:"Roboto Condensed",sans-serif;color:var(--white);text-decoration:none;font-size:13.5px;padding:0 22px;line-height:52px;text-transform:uppercase}
.nav a.active{background:var(--green-dark)}
/* hero */
.hero{top:210px;left:0;width:1200px;height:570px;overflow:hidden}
.hero-photo{width:100%;height:100%;background:linear-gradient(100deg,#8c6a1e 0%,#b59a45 35%,#dccfa8 62%,#e9e1cd 80%,#a7b567 100%)}
.hero-copy{left:107px;top:170px;width:440px;color:var(--white)}
.hero-copy h1{font-family:"Roboto Condensed",sans-serif;font-weight:700;font-size:34px;line-height:42px}
.hero-copy p{font-size:12.5px;line-height:19px;margin-top:14px}
.btn-orange{display:inline-block;background:var(--orange);color:var(--white);font-size:13px;padding:10px 16px;margin-top:18px;border-radius:2px;text-transform:uppercase}
.arrow{top:242px;width:34px;height:34px;border-radius:50%;background:rgba(0,0,0,.75);display:flex;align-items:center;justify-content:center}
.wave{left:0;bottom:0}
/* offers */
.section-title{font-size:27px;font-weight:400;text-align:center;color:#2b2b2b;text-transform:uppercase;line-height:36px}
.offers-title{top:830px;left:0;width:1200px}
.offer{top:940px;width:300px;text-align:center}
.offer .icon{width:104px;height:104px;margin:0 auto;border-radius:50%;border:3px solid var(--orange);padding:4px}
.offer .icon div{width:100%;height:100%;border-radius:50%;background:var(--green-dark);display:flex;align-items:center;justify-content:center}
.offer h3{font-size:18px;font-weight:400;margin-top:22px;color:#2b2b2b}
.offer p{font-size:11.5px;color:var(--muted);line-height:19px;margin-top:12px}
.more{font-size:12.5px;color:var(--green);margin-top:16px}
/* welcome */
.welcome{top:1270px;left:0;width:1200px;height:450px;background:var(--grey-band)}
.video{left:108px;top:80px;width:432px;height:298px;border:4px solid var(--white);box-shadow:0 0 3px #bbb;background:linear-gradient(160deg,#b68a3f,#d1b270 40%,#7f8f4a 75%,#5d6e36)}
.play{left:190px;top:120px;width:52px;height:52px;border-radius:50%;border:2px solid #fff;background:rgba(255,255,255,.35);display:flex;align-items:center;justify-content:center}
.welcome-copy{left:590px;top:85px;width:500px}
.welcome-copy h2{font-size:29px;font-weight:400;color:#2b2b2b}
.welcome-copy .lead{font-size:13.5px;font-weight:500;line-height:21px;margin-top:14px}
.welcome-copy p{font-size:11.5px;line-height:20px;color:#555;margin-top:12px}
.btn-green{display:inline-block;background:var(--green);color:var(--white);font-size:13px;padding:9px 18px;margin-top:18px;text-transform:uppercase}
/* services */
.services-title{top:1790px;left:0;width:1200px}
.services-intro{top:1845px;left:250px;width:700px;font-size:11.5px;line-height:21px;color:#555;text-align:center}
.service{top:1945px;width:260px;text-align:center}
.service .photo{width:210px;height:210px;margin:0 auto;border-radius:50%;border:9px solid var(--green-dark)}
.service h4{font-size:13.5px;font-weight:500;margin-top:24px;text-transform:uppercase}
.service p{font-size:11.5px;line-height:20px;color:#666;margin-top:12px;padding:0 22px}
.service .chev{margin-top:14px}
/* testimonial */
.testimonial{top:2395px;left:0;width:1200px;height:220px;background:#f0f0f0}
.avatar{left:158px;top:35px;width:150px;height:150px;border-radius:50%;background:radial-gradient(circle at 50% 40%,#d9c7b3,#b39a83 60%,#8d7a66)}
.quote{left:340px;top:55px;width:740px;font-size:13px;font-style:italic;line-height:22px;color:#555}
.quote .who{color:var(--green);font-size:15px;margin-top:12px}
.bigq{right:110px;top:140px;font-size:60px;color:#ddd;font-family:Georgia,serif}
/* footer */
.footer{top:2615px;left:0;width:1200px;height:346px;background:var(--footer);color:var(--white)}
.fcol h5{font-size:15px;font-weight:500;text-transform:uppercase;margin-bottom:24px}
.fcol{top:50px;font-size:12.5px;line-height:18px}
.frow{display:flex;gap:16px;align-items:flex-start;margin-bottom:16px}
.input{background:var(--white);color:#666;font-size:11px;height:40px;width:285px;padding:13px 14px;margin-top:20px}
.subscribe{display:inline-block;background:var(--green);font-size:12px;padding:12px 14px;margin-top:16px;text-transform:uppercase}
.links div{margin-bottom:6px}
.social div{display:flex;align-items:center;gap:10px;margin-bottom:15px;font-size:13px}
.social .c{width:24px;height:24px;border:1px solid #ddd;border-radius:50%}
.copyright{bottom:20px;left:0;width:1200px;text-align:center;font-size:12px;color:#ddd}
</style>
</head>
<body>

<header class="header abs">
  <div class="contact-top abs">
    <div class="ring"><svg width="16" height="16" viewBox="0 0 24 24"><path d="M6.6 10.8a15 15 0 006.6 6.6l2.2-2.2c.3-.3.7-.4 1-.2 1.1.4 2.3.6 3.6.6.6 0 1 .4 1 1V20c0 .6-.4 1-1 1A17 17 0 013 4c0-.6.4-1 1-1h3.5c.6 0 1 .4 1 1 0 1.3.2 2.5.6 3.6.1.3 0 .7-.2 1z" fill="#777"/></svg></div>
    <div>Call Us : +1 (555) 214-0387<br><small>info@vellisant.com</small></div>
  </div>
  <div class="brand abs">
    <div class="name">VELLISANT</div>
  </div>
  <div class="search abs"><span>search</span>
    <svg width="12" height="12" viewBox="0 0 24 24"><circle cx="10" cy="10" r="7" fill="none" stroke="#333" stroke-width="3"/><path d="M15 15l6 6" stroke="#333" stroke-width="3"/></svg>
  </div>
</header>

<nav class="nav abs">
  <a class="active">Home</a><a>Assisted Living</a><a>Skilled Nursing</a><a>Independent Living</a><a>Respite Care</a><a>Rehabilitation</a><a>Blog</a><a>Contact Us</a>
</nav>

<section class="hero abs">
  <div class="hero-photo" role="img" aria-label="Photo of a smiling senior couple outdoors in warm sunlight"></div>
  <div class="hero-copy abs">
    <h1>COMPREHENSIVE<br>PRIMARY CARE SERVICES</h1>
    <p>Sed ut perspiciatis unde omnis iste natus error sit voluptatem accusantium doloremque laudantium, totam rem</p>
    <span class="btn-orange">Get a free quote</span>
  </div>
  <div class="arrow abs" style="left:35px"><svg width="12" height="12" viewBox="0 0 12 12"><path d="M8 1L3 6l5 5" stroke="#fff" stroke-width="2" fill="none"/></svg></div>
  <div class="arrow abs" style="left:1141px"><svg width="12" height="12" viewBox="0 0 12 12"><path d="M4 1l5 5-5 5" stroke="#fff" stroke-width="2" fill="none"/></svg></div>
  <svg class="wave abs" width="1200" height="110" viewBox="0 0 1200 110">
    <path d="M0 70 C300 -10 700 20 1200 40 L1200 110 L0 110Z" fill="var(--green)"/>
    <path d="M0 85 C300 5 700 30 1200 55 L1200 110 L0 110Z" fill="var(--orange)"/>
    <path d="M0 100 C300 20 700 40 1200 70 L1200 110 L0 110Z" fill="#fff"/>
  </svg>
</section>

<h2 class="section-title offers-title abs">Vellisant offers home<br>and community</h2>

<div class="offer abs" style="left:102px">
  <div class="icon"><div><svg width="46" height="46" viewBox="0 0 24 24" fill="none" stroke="#fff" stroke-width="1.8"><path d="M6 3v6a4 4 0 008 0V3M10 13v3a4 4 0 008 0v-3"/><circle cx="18" cy="11" r="2"/></svg></div></div>
  <h3>Chronic Care Management</h3>
  <p>Sed ut perspiciatis unde omnis iste natus error sit voluptatem accusantium doloremque laudantium, totam rem aperiam, eaque ipsa quae</p>
  <div class="more">Read More »</div>
</div>
<div class="offer abs" style="left:450px">
  <div class="icon"><div><svg width="46" height="46" viewBox="0 0 24 24" fill="none" stroke="#fff" stroke-width="1.8"><path d="M12 21V9M12 14l-4-3M12 12l4-3"/><circle cx="12" cy="6" r="2"/><circle cx="6" cy="9" r="1.6"/><circle cx="18" cy="7" r="1.6"/></svg></div></div>
  <h3>Physical Therapy</h3>
  <p>Sed ut perspiciatis unde omnis iste natus error sit voluptatem accusantium doloremque laudantium, totam rem aperiam, eaque ipsa quae</p>
  <div class="more">Read More »</div>
</div>
<div class="offer abs" style="left:805px">
  <div class="icon"><div><svg width="46" height="46" viewBox="0 0 24 24"><rect x="3" y="7" width="18" height="13" rx="2" fill="#fff"/><path d="M9 7V4h6v3" stroke="#fff" stroke-width="1.8" fill="none"/><path d="M12 10v7M8.5 13.5h7" stroke="var(--green-dark)" stroke-width="2.4"/></svg></div></div>
  <h3>Medications Management</h3>
  <p>Sed ut perspiciatis unde omnis iste natus error sit voluptatem accusantium doloremque laudantium, totam rem aperiam, eaque ipsa quae</p>
  <div class="more">Read More »</div>
</div>

<section class="welcome abs">
  <div class="video abs" role="img" aria-label="Video still of a senior couple jogging in an autumn park">
    <div class="play abs"><svg width="18" height="18" viewBox="0 0 18 18"><path d="M5 3l10 6-10 6z" fill="#555"/></svg></div>
  </div>
  <div class="welcome-copy abs">
    <h2>WELCOME TO VELLISANT</h2>
    <div class="lead">Vellisant offers home and Community Based Services for adults who wish to continue live independently in their communities.</div>
    <p>We provide on site services and deliver high quality healthcare at your door. Our experienced physicians coordinate care with our certified nurse practitioners and provide chronic care management, physical therapy, rehabilitation and medications management.</p>
    <p>Sed ut perspiciatis unde omnis iste natus error sit voluptatem accusantium doloremque laudantium, totam rem aperiam, eaque ipsa quae ab illo inventore veritatis et quasi architecto beatae vitae dicta sunt explicabo.</p>
    <span class="btn-green">Read more</span>
  </div>
</section>

<h2 class="section-title services-title abs">Our services</h2>
<p class="services-intro abs">Sed ut perspiciatis unde omnis iste natus error sit voluptatem accusantium doloremque laudantium, totam rem aperiam, eaque ipsa quae ab illo inventore veritatis et quasi architecto beatae vitae dicta sunt explicabo.</p>

<div class="service abs" style="left:73px">
  <div class="photo" role="img" aria-label="Photo of a caregiver assisting a senior man" style="background:linear-gradient(150deg,#e8e2d6,#c9b79c 55%,#8ea36a)"></div>
  <h4>Comprehensive Primary</h4>
  <p>Sed ut perspiciatis unde omnis iste natus error sit voluptatem accusantium doloremque laudantium</p>
  <div class="chev"><svg width="12" height="10" viewBox="0 0 12 10"><path d="M2 1l4 3 4-3M2 5l4 3 4-3" stroke="#333" stroke-width="1.5" fill="none"/></svg></div>
</div>
<div class="service abs" style="left:335px">
  <div class="photo" role="img" aria-label="Photo of a smiling senior couple" style="background:linear-gradient(150deg,#9fbf55,#d9b98f 50%,#b08a66)"></div>
  <h4>Dental Health</h4>
  <p>Sed ut perspiciatis unde omnis iste natus error sit voluptatem accusantium doloremque laudantium</p>
  <div class="chev"><svg width="12" height="10" viewBox="0 0 12 10"><path d="M2 1l4 3 4-3M2 5l4 3 4-3" stroke="#333" stroke-width="1.5" fill="none"/></svg></div>
</div>
<div class="service abs" style="left:605px">
  <div class="photo" role="img" aria-label="Photo of a senior couple relaxing on a sofa at home" style="background:linear-gradient(150deg,#dcdcdc,#c2b6a6 55%,#9b8f80)"></div>
  <h4>Home Health Assistance</h4>
  <p>Sed ut perspiciatis unde omnis iste natus error sit voluptatem accusantium doloremque laudantium</p>
  <div class="chev"><svg width="12" height="10" viewBox="0 0 12 10"><path d="M2 1l4 3 4-3M2 5l4 3 4-3" stroke="#333" stroke-width="1.5" fill="none"/></svg></div>
</div>
<div class="service abs" style="left:867px">
  <div class="photo" role="img" aria-label="Photo of a joyful senior woman outdoors in a garden" style="background:linear-gradient(150deg,#a9c46a,#6f9a3a 50%,#d7b640)"></div>
  <h4>Mental Health</h4>
  <p>Sed ut perspiciatis unde omnis iste natus error sit voluptatem accusantium doloremque laudantium</p>
  <div class="chev"><svg width="12" height="10" viewBox="0 0 12 10"><path d="M2 1l4 3 4-3M2 5l4 3 4-3" stroke="#333" stroke-width="1.5" fill="none"/></svg></div>
</div>

<section class="testimonial abs">
  <svg class="abs" style="left:150px;top:30px" width="168" height="168" viewBox="0 0 168 168"><path d="M10 84a74 74 0 00148 0" stroke="var(--green)" stroke-width="6" fill="none"/></svg>
  <div class="avatar abs" role="img" aria-label="Portrait photo of a smiling senior man"></div>
  <div class="quote abs">“ Sed ut perspiciatis unde omnis iste natus error sit voluptatem accusantium doloremque laudantium, totam rem aperiam, eaque ipsa quae ab illo inventore veritatis et quasi architecto beatae vitae dicta sunt explicabo. Nemo enim ipsam voluptatem quia voluptas sit aspernatur aut odit aut fugit, sed quia consequuntur
    <div class="who">Martin Hale - Vellisant</div>
  </div>
  <div class="bigq abs">”</div>
</section>

<footer class="footer abs">
  <div class="fcol abs" style="left:100px;width:300px">
    <h5>Contact us</h5>
    <div class="frow"><svg width="16" height="20" viewBox="0 0 16 20"><path d="M8 1a6 6 0 016 6c0 5-6 12-6 12S2 12 2 7a6 6 0 016-6z" fill="none" stroke="#fff" stroke-width="1.5"/><circle cx="8" cy="7" r="2" fill="#fff"/></svg><div>Vellisant<br>4120 LM, Brookhaven Fieldstone.</div></div>
    <div class="frow"><svg width="16" height="16" viewBox="0 0 24 24"><path d="M6.6 10.8a15 15 0 006.6 6.6l2.2-2.2c.3-.3.7-.4 1-.2 1.1.4 2.3.6 3.6.6.6 0 1 .4 1 1V20c0 .6-.4 1-1 1A17 17 0 013 4c0-.6.4-1 1-1h3.5c.6 0 1 .4 1 1 0 1.3.2 2.5.6 3.6.1.3 0 .7-.2 1z" fill="#fff"/></svg><div>Phone : 555 0192 7730</div></div>
    <div class="frow"><svg width="18" height="14" viewBox="0 0 18 14"><rect x="1" y="1" width="16" height="12" fill="none" stroke="#fff" stroke-width="1.4"/><path d="M1 1l8 7 8-7" fill="none" stroke="#fff" stroke-width="1.4"/></svg><div>info@vellisant.com</div></div>
  </div>
  <div class="fcol abs" style="left:430px;width:300px">
    <h5>Sign up to receive email</h5>
    <div style="font-size:11.5px;line-height:18px">Excepteur sint occaecat cupidatat non proident, sunt in culpa qui Nemo enim ipsam voluptatem</div>
    <div class="input">Enter Name</div>
    <span class="subscribe">Subscribe</span>
  </div>
  <div class="fcol links abs" style="left:810px;width:170px;font-size:12px">
    <h5>Quick links</h5>
    <div>Home</div><div>Assisted Living</div><div>Skilled Nursing</div><div>Independent Living</div><div>Home and Community</div><div>Respite Care</div><div>Rehabilitation</div>
  </div>
  <div class="fcol social abs" style="left:1000px;width:150px">
    <h5>Social media</h5>
    <div><span class="c"></span>Vemora</div>
    <div><span class="c"></span>Tallok</div>
    <div><span class="c"></span>Quistry</div>
    <div><span class="c"></span>Zunavid</div>
  </div>
  <div class="copyright abs">Copyright © Vellisant 2017. All rights reserved.</div>
</footer>

</body>
</html>
```